Structural Engineering Business Card

Brookvane Drafting does residential house plans for clients in Central Florida. Would like simple but elegant business card that is appropriate for a house plan engineering company. Prefer black business card with black/white them but open to other shades of blue. I uploaded a sample card that I came across that looked good but please come up with your own creative designs.

Contact Information for Business Card

Name, Title, Phone, Email, Address, website

```html
<!DOCTYPE html>
<html lang="en">
<head>
<meta charset="utf-8">
<title>Brookvane Drafting – Business Card</title>
<link rel="stylesheet" href="https://fonts.googleapis.com/css2?family=Montserrat:wght@700;800&family=Nunito+Sans:wght@400;600&display=swap">
<style>
  :root {
    --ink: #050505;
    --paper: #ffffff;
    --frost-top: #efe8e8;
    --frost-bottom: #f8f4f4;
    --stage: #dcdcdc;
  }
  * { box-sizing: border-box; margin: 0; padding: 0; }
  html, body {
    width: 1200px; height: 900px; overflow: hidden;
    background: var(--stage);
  }
  .card {
    position: absolute; left: 100px; top: 141px;
    width: 1000px; height: 618px;
    background: linear-gradient(180deg, var(--frost-top), var(--frost-bottom));
    overflow: hidden;
    box-shadow: 0 10px 30px rgba(0,0,0,.18);
  }
  .card__wave { position: absolute; inset: 0; width: 100%; height: 100%; }
  .brand {
    position: absolute; left: 58px; top: 150px;
    display: flex; align-items: center; gap: 16px;
    font-family: "Montserrat", sans-serif; font-weight: 800;
    font-size: 52px; letter-spacing: -0.5px; color: var(--ink);
  }
  .brand__mark { width: 34px; height: 34px; background: var(--ink); }
  .person {
    position: absolute; left: 60px; top: 430px; color: var(--paper);
  }
  .person__name {
    font-family: "Montserrat", sans-serif; font-weight: 700;
    font-size: 38px; line-height: 1.1;
  }
  .person__title {
    font-family: "Nunito Sans", sans-serif; font-weight: 400;
    font-size: 27px; margin-top: 2px;
  }
  .contact {
    position: absolute; right: 68px; top: 362px;
    color: var(--paper); text-align: right;
    font-family: "Nunito Sans", sans-serif; font-size: 27px; line-height: 36px;
  }
  .contact__line { display: flex; justify-content: flex-end; align-items: center; gap: 16px; }
  .contact__icon { width: 26px; height: 26px; flex: none; }
  .contact__address { margin-top: 18px; }
</style>
</head>
<body>
  <section class="card" aria-label="Brookvane Drafting business card">
    <svg class="card__wave" viewBox="0 0 1090 674" preserveAspectRatio="none" aria-hidden="true">
      <path fill="#ffffff" d="M0,338 C160,415 330,410 520,350 C680,300 760,282 820,281 C950,280 1040,320 1090,342 L1090,674 L0,674 Z"/>
      <path fill="#050505" d="M0,382 C170,420 330,415 520,360 C680,310 760,284 820,283 C950,282 1040,322 1090,345 L1090,674 L0,674 Z"/>
    </svg>

    <div class="brand">
      <span class="brand__mark"></span>
      <span class="brand__name">Brookvane Drafting</span>
    </div>

    <div class="person">
      <p class="person__name">DANIEL HARTWELL</p>
      <p class="person__title">Managing Director</p>
    </div>

    <div class="contact">
      <p class="contact__line">044-321 654 987
        <svg class="contact__icon" viewBox="0 0 24 24" fill="none" stroke="#fff" stroke-width="2" stroke-linecap="round" stroke-linejoin="round"><path d="M5 3h3l2 5-2.5 1.5a11 11 0 0 0 7 7L16 14l5 2v3a2 2 0 0 1-2 2A17 17 0 0 1 3 5a2 2 0 0 1 2-2z"/><path d="M14 3a7 7 0 0 1 7 7M14 7a3 3 0 0 1 3 3"/></svg>
      </p>
      <p class="contact__line">info@brookvane.com
        <svg class="contact__icon" viewBox="0 0 24 24" fill="none" stroke="#fff" stroke-width="2" stroke-linejoin="round"><rect x="2" y="5" width="20" height="14"/><path d="M2 5l10 8 10-8M2 19l7-7M22 19l-7-7"/></svg>
      </p>
      <p class="contact__line">www.brookvane.com
        <svg class="contact__icon" viewBox="0 0 24 24" fill="none" stroke="#fff" stroke-width="2"><circle cx="12" cy="12" r="10"/><ellipse cx="12" cy="12" rx="4.5" ry="10"/><path d="M2 12h20M4 7h16M4 17h16"/></svg>
      </p>
      <p class="contact__address">318, Cypress Hollow Lane<br>Ocoee 34761,United States</p>
    </div>
  </section>
</body>
</html>
```